Heron Haulage needs Bussiness cards!

Our new trucking company needs business cards!
We need the same design with two different names and emails, everything else it's the same.
I have included our original logo so we can use it for the design.
Note: the logo to be used is the o e with the buffalo on the right side, next to the letters H and H.

Target Market(s)

Trucking, refrigerated transportation, freight

Industry/Entity Type

Business

Contact Information for Business Card

Card #1:
Marcus Whitfield
marcuswhitfield@heronhaulage.example
1-855-317-6094
(956)238-7160
4117 W. Larkin Ave.
Pharr, TX 78590
www.heronhaulage.example

Card#2:
Rosalba Quintero
rosalba@heronhaulage.example
1-855-317-6094
(956)238-7160
4117 W. Larkin Ave.
Pharr, TX 78590
www.heronhaulage.example

Font styles to use
Sans Serif

Colors
0655a3
ec1f27
ffffff

Requirements
Must have
• our logo
Nice to have
• roads on background,

```html
<!DOCTYPE html>
<html lang="en">
<head>
<meta charset="utf-8">
<title>Heron Haulage – Business Card</title>
<link href="https://fonts.googleapis.com/css2?family=Open+Sans:wght@400;600;700;800&display=swap" rel="stylesheet">
<style>
  :root{
    --navy:#0b2b57;
    --blue:#0655a3;
    --sky:#1a8fd6;
    --red:#c8161e;
    --white:#ffffff;
    --paper:#ececec;
  }
  *{margin:0;padding:0;box-sizing:border-box}
  html,body{width:1200px;height:900px;overflow:hidden}
  body{background:var(--paper);font-family:"Open Sans",Arial,sans-serif;position:relative}

  .card{position:absolute;overflow:hidden;box-shadow:0 6px 18px rgba(0,0,0,.18)}

  /* Front */
  .card-front{left:78px;top:33px;width:588px;height:365px;background:var(--navy)}
  .front-top-band{position:absolute;left:0;top:0;width:100%;height:58px;background:var(--red)}
  .front-top-line{position:absolute;left:0;top:36px;width:100%;height:6px;background:var(--white)}
  .front-art{position:absolute;right:0;top:0;width:250px;height:100%}
  .holder{position:absolute;left:31px;top:117px;color:var(--white)}
  .holder-name{font-size:21px;font-weight:700;letter-spacing:.1px}
  .holder-address{margin-top:20px;font-size:15px;line-height:25px}
  .contact-list{list-style:none;margin-top:20px;font-size:15px;line-height:24.5px}
  .contact-list li{display:flex;align-items:center;gap:9px}
  .contact-list svg{width:13px;height:13px;fill:var(--white);flex:none}

  /* Back */
  .card-back{left:388px;top:505px;width:566px;height:352px;background:var(--white)}
  .brand{position:absolute;left:0;top:160px;width:100%;display:flex;justify-content:center;align-items:center;gap:14px}
  .brand-name{font-size:44px;font-weight:800;color:var(--navy);letter-spacing:-.5px}
  .brand-dot{width:26px;height:26px;border-radius:50%;background:var(--red)}
  .back-band{position:absolute;left:0;top:285px;width:100%;height:48px;background:var(--navy);
    color:var(--white);font-size:19px;display:flex;align-items:center;justify-content:center}
  .back-stripe{position:absolute;left:0;top:333px;width:100%;height:19px;background:var(--red)}
</style>
</head>
<body>

<section class="card card-front">
  <div class="front-top-band"></div>
  <div class="front-top-line"></div>
  <svg class="front-art" viewBox="0 0 250 365" role="img" aria-label="Illustration of a charging animal head mascot in navy, blue and white">
    <defs>
      <linearGradient id="artTone" x1="0" y1="0" x2="1" y2="1">
        <stop offset="0" stop-color="#0655a3"/>
        <stop offset="1" stop-color="#0b2b57"/>
      </linearGradient>
    </defs>
    <rect width="250" height="365" fill="#ffffff"/>
    <path d="M0 0 H170 C230 60 250 150 245 240 C240 320 200 365 160 365 H0 Z" fill="url(#artTone)"/>
  </svg>

  <div class="holder">
    <h1 class="holder-name">Marcus Whitfield</h1>
    <p class="holder-address">4117 W. Larkin Ave.<br>Pharr, TX 78590</p>
    <ul class="contact-list">
      <li><svg viewBox="0 0 24 24"><path d="M6.6 10.8a15.1 15.1 0 0 0 6.6 6.6l2.2-2.2a1 1 0 0 1 1-.25 11.4 11.4 0 0 0 3.6.57 1 1 0 0 1 1 1V20a1 1 0 0 1-1 1A17 17 0 0 1 3 4a1 1 0 0 1 1-1h3.5a1 1 0 0 1 1 1c0 1.25.2 2.45.57 3.57a1 1 0 0 1-.25 1z"/></svg>1-855-317-6094</li>
      <li><svg viewBox="0 0 24 24"><path d="M7 1h10a2 2 0 0 1 2 2v18a2 2 0 0 1-2 2H7a2 2 0 0 1-2-2V3a2 2 0 0 1 2-2zm0 3v14h10V4zm5 15.5a1.2 1.2 0 1 0 0 2.4 1.2 1.2 0 0 0 0-2.4z"/></svg>(956)238-7160</li>
      <li><svg viewBox="0 0 24 24"><path d="M2 5h20v14H2zm2 2v.5l8 5 8-5V7zm0 2.8V17h16V9.8l-8 5z"/></svg>marcuswhitfield@heronhaulage.example</li>
      <li><svg viewBox="0 0 24 24"><path d="M12 2a10 10 0 1 0 0 20 10 10 0 0 0 0-20zm6.9 6h-2.9a15 15 0 0 0-1.4-3.9A8 8 0 0 1 18.9 8zM12 4c.8 1.2 1.5 2.5 1.9 4h-3.8c.4-1.5 1.1-2.8 1.9-4zM4.3 14a8 8 0 0 1 0-4h3.4a16 16 0 0 0 0 4zm.8 2h2.9c.3 1.4.8 2.7 1.4 3.9A8 8 0 0 1 5.1 16zM8 8H5.1a8 8 0 0 1 4.3-3.9C8.8 5.3 8.3 6.6 8 8zm4 12c-.8-1.2-1.5-2.5-1.9-4h3.8c-.4 1.5-1.1 2.8-1.9 4zm2.3-6H9.7a14 14 0 0 1 0-4h4.6a14 14 0 0 1 0 4zm.3 5.9c.6-1.2 1.1-2.5 1.4-3.9h2.9a8 8 0 0 1-4.3 3.9zM16.3 14a16 16 0 0 0 0-4h3.4a8 8 0 0 1 0 4z"/></svg>www.heronhaulage.example</li>
    </ul>
  </div>
</section>

<section class="card card-back">
  <div class="brand">
    <span class="brand-name">Heron Haulage</span>
    <span class="brand-dot"></span>
  </div>
  <div class="back-band">www.heronhaulage.example</div>
  <div class="back-stripe"></div>
</section>

</body>
</html>
```